Ferncrest Roam Wording For Logo & Business card

I have the logo, I just need the "Ferncrest Roam" wording to go with it, and a business card design. The only thing on the business card is the website info. We provide nature connection experiences, and bolster these efforts through writing and host a platform for community around it.

I also have an idea of what it could look like (sketch), though I'm really not sure how it would come out. I am open to the best design and happy to consider original artwork. You can see what the site is about at FerncrestRoam.example.

Contact Information for Business Card

The only thing on the business card is the website info and the design. I will put other messaging on the back.

Website lettering (FerncrestRoam.example) in Montserrat

Logo Text

Ferncrest Roam (letters optional)

Font styles to use
Other font styles liked:
• montserrat

```html
<!DOCTYPE html>
<html lang="en">
<head>
<meta charset="utf-8">
<title>Ferncrest Roam — Business Card</title>
<link rel="stylesheet" href="https://fonts.googleapis.com/css2?family=Montserrat:wght@300;400&display=swap">
<style>
  :root {
    --backdrop: #2c2c2c;
    --card: #ffffff;
    --ink: #1d1b22;
    --accent: #f7941d;
    --mark: #2a1b3d;
  }
  * { box-sizing: border-box; margin: 0; padding: 0; }
  html, body {
    width: 1200px; height: 583px; overflow: hidden;
    background: var(--backdrop);
    font-family: "Montserrat", Arial, sans-serif;
    color: var(--ink);
  }
  .stage { position: relative; width: 1200px; height: 583px; }
  .card {
    position: absolute; top: 154px;
    width: 481px; height: 275px;
    background: var(--card);
    border-radius: 40px;
    overflow: hidden;
  }
  .card--front { left: 94px; }
  .card--back  { left: 627px; }

  .brand {
    position: absolute; left: 78px; top: 97px;
    display: flex; align-items: center; gap: 12px;
  }
  .brand__dot {
    width: 72px; height: 72px; border-radius: 50%;
    background: var(--mark); flex: none;
  }
  .brand__name {
    font-weight: 300; font-size: 25px; letter-spacing: 2.5px;
    text-transform: uppercase; white-space: nowrap;
  }

  .rule {
    position: absolute; left: 0; right: 0; top: 229px;
    height: 1px; background: var(--ink);
  }
  .pill {
    position: absolute; top: 219px; left: 50%;
    transform: translateX(-50%);
    height: 20px; padding: 0 9px;
    display: flex; align-items: center; gap: 4px;
    background: var(--card);
    border: 1px solid var(--ink); border-radius: 10px;
    white-space: nowrap;
  }
  .pill--web {
    font-size: 13px; font-weight: 300; letter-spacing: 4.2px;
  }
  .pill--web .web-name { color: var(--accent); }
  .pill--contact { font-size: 10.5px; font-weight: 400; letter-spacing: -0.2px; }
  .icon { width: 10px; height: 10px; flex: none; }
  .pill--contact .icon + span { margin-right: 3px; }

  .holder {
    position: absolute; left: 0; right: 0; top: 31px;
    display: flex; flex-direction: column; align-items: center;
  }
  .holder__mark {
    width: 134px; height: 134px; border-radius: 50%;
    background: var(--mark);
  }
  .holder__name {
    margin-top: 12px;
    font-weight: 400; font-size: 22px; letter-spacing: 3px;
    text-transform: uppercase;
  }
</style>
</head>
<body>
<main class="stage">
  <section class="card card--front">
    <div class="brand">
      <div class="brand__dot"></div>
      <span class="brand__name">Ferncrest Roam</span>
    </div>
    <div class="rule"></div>
    <div class="pill pill--web">www.<span class="web-name">ferncrestroam</span>.example</div>
  </section>

  <section class="card card--back">
    <div class="holder">
      <div class="holder__mark"></div>
      <p class="holder__name">Jordan Vale</p>
    </div>
    <div class="rule"></div>
    <div class="pill pill--contact">
      <svg class="icon" viewBox="0 0 10 10" aria-hidden="true">
        <circle cx="5" cy="5" r="5" fill="#f7941d"/>
        <path d="M3.2 2.4l1 .9-.5.8c.4.8 1 1.4 1.8 1.8l.8-.5.9 1-.7.8C4.8 7.2 2.8 5.2 2.4 3.2z" fill="#fff"/>
      </svg>
      <span>555-014-2200</span>
      <svg class="icon" viewBox="0 0 10 10" aria-hidden="true">
        <circle cx="5" cy="5" r="5" fill="#f7941d"/>
        <path d="M5 2a2 2 0 0 0-2 2c0 1.5 2 4 2 4s2-2.5 2-4a2 2 0 0 0-2-2zm0 2.8a.8.8 0 1 1 0-1.6.8.8 0 0 1 0 1.6z" fill="#fff"/>
      </svg>
      <span>your address,your city,box 88900</span>
    </div>
  </section>
</main>
</body>
</html>
```